Vormel Building Pty Ltd need an Identity!

We need a logo design for a building company based in Sydney, Australia. In addition - Business Card Layout. The colour scheme is to be black and red and communicate a professional yet 'hands on' approach to building.

Target Market(s)

Architects, Home Owners, Developers

Industry/Entity Type

Construction

Font styles to use
Serif
Sans Serif

Colors
ec1f27

Requirements
Must have
• Clear logo and professional direction.
Nice to have
• Use of initials as a possible logo
Should not have
• Graphics/pictures of houses, house roofs etc. Can be an abstracted form of a building.

```html
<!DOCTYPE html>
<html lang="en">
<head>
<meta charset="utf-8">
<title>Vormel Building Pty Ltd — Business Cards</title>
<link rel="stylesheet" href="https://fonts.googleapis.com/css2?family=Roboto:wght@400;500;700&display=swap">
<style>
  :root {
    --canvas-bg: #cbcbcb;
    --card-dark: #3e4346;
    --card-light: #fafafa;
    --brand-red: #ec1f27;
    --ink: #3e4346;
    --ink-soft: #4a4f52;
    --on-dark: #e2e2e2;
  }
  * { margin: 0; padding: 0; box-sizing: border-box; }
  html, body {
    width: 1200px; height: 1005px; overflow: hidden;
    background: var(--canvas-bg);
    font-family: "Roboto", Arial, sans-serif;
  }
  .card {
    position: absolute; left: 280px;
    width: 640px; height: 366px;
    box-shadow: 0 6px 14px rgba(0,0,0,0.22);
  }
  .card--front { top: 100px; background: var(--card-dark); }
  .card--back  { top: 520px; background: var(--card-light); }

  .wordmark {
    font-weight: 700; letter-spacing: -0.5px; white-space: nowrap;
  }
  .card--front .wordmark {
    position: absolute; left: 0; right: 0; top: 160px;
    text-align: center; font-size: 38px; color: var(--on-dark);
  }
  .card--back .wordmark {
    position: absolute; right: 40px; top: 40px;
    font-size: 30px; color: var(--ink);
  }

  .holder {
    position: absolute; left: 0; top: 120px;
    padding-left: 52px;
  }
  .holder__bar {
    position: absolute; left: 18px; top: 2px;
    width: 18px; height: 62px; background: var(--brand-red);
  }
  .holder__name { font-size: 24px; font-weight: 700; color: var(--ink); }
  .holder__role { font-size: 15px; color: var(--ink-soft); margin-top: 4px; }

  .contacts {
    position: absolute; left: 70px; bottom: 34px;
    list-style: none; font-size: 15px; color: var(--ink-soft);
  }
  .contacts li { display: flex; align-items: center; gap: 10px; line-height: 24px; }
  .contacts svg { width: 14px; height: 14px; fill: var(--brand-red); flex: none; }
  .contacts .address { padding-left: 0; margin-top: 4px; }
</style>
</head>
<body>
  <section class="card card--front">
    <div class="wordmark">Vormel Building Pty Ltd</div>
  </section>

  <section class="card card--back">
    <div class="wordmark">Vormel Building Pty Ltd</div>

    <div class="holder">
      <span class="holder__bar"></span>
      <div class="holder__name">Daniel Reeve</div>
      <div class="holder__role">Managing Director</div>
    </div>

    <ul class="contacts">
      <li>
        <svg viewBox="0 0 16 16" aria-hidden="true"><path d="M3.5 1l2.5 3-1.5 1.5c.8 2 2.5 3.7 4.5 4.5L10.5 8.5l3 2.5-1.5 3C6.5 14 2 9.5 2 2.5z"/></svg>
        1300 481 902
      </li>
      <li>
        <svg viewBox="0 0 16 16" aria-hidden="true"><circle cx="8" cy="8" r="7"/><path d="M1 8h14M8 1c-3 3-3 11 0 14M8 1c3 3 3 11 0 14" stroke="#fafafa" stroke-width="1" fill="none"/></svg>
        www.vormelbuilding.com.au
      </li>
      <li>
        <svg viewBox="0 0 16 16" aria-hidden="true"><rect x="1" y="3" width="14" height="10"/><path d="M1 3l7 6 7-6" stroke="#fafafa" stroke-width="1.2" fill="none"/></svg>
        daniel.reeve@vormelbuilding.com.au
      </li>
      <li class="address">48 Harbour Row, Sydney NSW 2000</li>
    </ul>
  </section>
</body>
</html>
```